Brightfield Ventures Inc. Letterhead

Creation of attractive and eye catching letterhead for a business start-up for the construction industry. Letterhead must relate to construction, but avoid standard hammer and tools in the design.

I forgot to add some details, sorry about that. Some pertinent info: Ph: 916-555-0187 brightfieldventures.example 448 Willowmere Ave, Ste 210 Folsom, CA 95999 info@brightfieldventures.example not sure if slogan should be in there" “Connecting construction professionals to create a purpose driven industry.” must be able to be used in word. Thanks!

```html
<!DOCTYPE html>
<html lang="en">
<head>
<meta charset="utf-8">
<title>Brightfield Ventures Inc. Letterhead</title>
<link href="https://fonts.googleapis.com/css2?family=Source+Sans+3:wght@400;600;700&family=Arimo:wght@700&display=swap" rel="stylesheet">
<style>
  :root {
    --brand-red: #b5090b;
    --brand-navy: #1b2856;
    --ink: #4a4a4a;
    --paper: #ffffff;
    --backdrop: #e9e9e9;
    --sign-fill: #f1f1f3;
  }
  html, body {
    margin: 0;
    width: 1200px;
    height: 1200px;
    overflow: hidden;
    background: var(--backdrop);
  }
  .letterhead {
    position: absolute;
    left: 189px;
    top: 20px;
    width: 822px;
    height: 1160px;
    background: var(--paper);
    font-family: "Source Sans 3", sans-serif;
    color: var(--ink);
  }
  .letterhead-frame {
    position: absolute;
    inset: 0;
    width: 100%;
    height: 100%;
  }
  .brand {
    position: absolute;
    left: 68px;
    top: 96px;
    width: 300px;
  }
  .brand-name {
    display: flex;
    align-items: center;
    gap: 10px;
    margin: 0;
    font-weight: 700;
    font-size: 24px;
    line-height: 28px;
    color: var(--brand-navy);
  }
  .brand-mark {
    width: 16px;
    height: 16px;
    background: var(--brand-red);
    flex: none;
  }
  .brand-slogan {
    margin: 8px 0 0;
    padding-top: 7px;
    border-top: 2px solid var(--brand-red);
    font-size: 12px;
    line-height: 15px;
    color: var(--brand-navy);
    width: 268px;
  }
  .contact {
    position: absolute;
    left: 614px;
    top: 22px;
    margin: 0;
    padding: 0;
    list-style: none;
    color: #fff;
    font-size: 11.5px;
    line-height: 16.5px;
  }
  .contact li { display: flex; align-items: center; gap: 6px; white-space: nowrap; }
  .contact svg { width: 9px; height: 9px; fill: #fff; flex: none; }
  .contact .address { margin-top: 7px; display: block; }
  .letter {
    position: absolute;
    left: 71px;
    top: 248px;
    width: 688px;
  }
  .salutation {
    margin: 0 0 17px;
    font-family: "Arimo", sans-serif;
    font-weight: 700;
    font-size: 18px;
    color: #555;
  }
  .letter p {
    margin: 0 0 21.4px;
    font-size: 17.4px;
    line-height: 21.4px;
    text-align: justify;
  }
  .signature {
    position: absolute;
    left: 69px;
    top: 800px;
    width: 151px;
    height: 76px;
    background: var(--sign-fill);
    border-radius: 4px;
  }
</style>
</head>
<body>
  <div class="letterhead">
    <svg class="letterhead-frame" viewBox="0 0 925 1305" preserveAspectRatio="none" aria-hidden="true">
      <path d="M0 0H925V136H690C660 136 650 120 635 90C618 50 605 22 560 20H0Z" fill="var(--brand-red)"/>
      <path d="M0 29H578C588 29 594 33 598 38H0Z" fill="var(--brand-navy)"/>
      <rect x="0" y="1254" width="925" height="51" fill="var(--brand-red)"/>
      <rect x="35" y="1244" width="855" height="24" rx="11" fill="var(--paper)"/>
      <rect x="43" y="1261" width="839" height="5" rx="2.5" fill="var(--brand-navy)"/>
    </svg>

    <header class="brand">
      <p class="brand-name"><span class="brand-mark"></span>Brightfield Ventures Inc.</p>
      <p class="brand-slogan">Connecting construction professionals to create a purpose driven industry.</p>
    </header>

    <ul class="contact">
      <li><svg viewBox="0 0 10 10"><path d="M2 0.5 3.6 2.6 2.7 3.7C3.3 5 4.6 6.4 6 7L7.2 6 9.5 7.6 8.6 9.5C4.5 9.5 0.5 5.5 0.5 1.4Z"/></svg>Ph: 916-555-0187</li>
      <li><svg viewBox="0 0 10 10"><path d="M0 2H10V8H0ZM0.8 2.6 5 5.6 9.2 2.6" stroke="var(--brand-red)" stroke-width="0.7"/></svg>info@brightfieldventures.example</li>
      <li><svg viewBox="0 0 10 10"><circle cx="5" cy="5" r="4.5"/><path d="M0.5 5H9.5M5 0.5V9.5" stroke="var(--brand-red)" stroke-width="0.7"/></svg>brightfieldventures.example</li>
      <li class="address">448 Willowmere Ave, Ste 210,<br>Folsom, CA 95999</li>
    </ul>

    <main class="letter">
      <h1 class="salutation">Dear Mr. John,</h1>
      <p>Lorem Ipsum is simply dummy text of the printing and typesetting industry. Lorem Ipsum has been the industry's standard dummy text ever since the 1500s, when an unknown printer took a galley of type and scrambled it to make a type specimen book. It has survived not only five centuries, but also the leap into electronic typesetting, remaining essentially unchanged.</p>
      <p>The standard chunk of Lorem Ipsum used since the 1500s is reproduced below for those interested. Sections 1.10.32 and 1.10.33 from "de Finibus Bonorum et Malorum" by Marcus Tullo are also reproduced in their exact original form, accompanied by English versions from the 1914 translation by H. Redmond</p>
      <p>Lorem Ipsum is simply dummy text of the printing and typesetting industry. Lorem Ipsum has been the industry's standard dummy text ever since the 1500s, when an unknown printer took a galley of type and scrambled it to make a type specimen book. It has survived not only five centuries, but also the leap into electronic typesetting, remaining essentially unchanged. It was popularised in the</p>
      <p>The standard chunk of Lorem Ipsum used since the 1500s is reproduced below for those interested. Sections 1.10.32 and 1.10.33 from "de Finibus Bonorum et Malorum" by Marcus Tullo are also reproduced in their exact original form, accompanied by English versions from the 1914 translation by H. Redmond</p>
    </main>

    <div class="signature" role="img" aria-label="Handwritten signature of the sender"></div>
  </div>
</body>
</html>
```